Business Card Design

Online clothing womens clothing store, I sell my clothing online and at the markets.

i would like the attached picture on the front of the card and the contact information on the back.

Industry/Entity Type

Business

Contact Information for Business Card

Marlow Thread
Karen Whitfield
(Instagram symbol) _marlow_thread_
(Facebook symbol) www.fakebookexample.com/marlowthreadau/

W : www.marlowthread.example.au
E : info@marlowthread.example.au
P : 0498716204

```html
<!DOCTYPE html>
<html lang="en">
<head>
<meta charset="utf-8">
<title>Marlow Thread — Business Card</title>
<link href="https://fonts.googleapis.com/css2?family=Open+Sans:wght@400;700&display=swap" rel="stylesheet">
<style>
  :root {
    --backdrop: #3a3230;
    --card-black: #0e0e0e;
    --ink-white: #f2f2f2;
    --ink-soft: #d8d8d8;
    --divider: #2c2c2c;
    --mist-light: #e4e8ea;
    --mist-teal: #a9c4c4;
    --mist-slate: #4c5458;
    --logo-dark: #2a2d30;
  }
  html, body {
    margin: 0;
    width: 1200px;
    height: 900px;
    overflow: hidden;
    background: var(--backdrop);
    font-family: "Open Sans", Arial, sans-serif;
  }
  .stage {
    position: relative;
    width: 1200px;
    height: 900px;
  }
  .card {
    position: absolute;
    top: 300px;
    width: 520px;
    height: 300px;
    box-shadow: 0 10px 24px rgba(0,0,0,0.45);
    overflow: hidden;
  }
  /* Back: contact side */
  .card-back {
    left: 50px;
    background: var(--card-black);
    color: var(--ink-white);
  }
  .back-wordmark {
    position: absolute;
    left: 0;
    width: 204px;
    top: 180px;
    text-align: center;
    font-size: 16px;
    font-weight: 400;
    letter-spacing: 1.5px;
    text-transform: uppercase;
    white-space: nowrap;
    color: var(--ink-white);
  }
  .back-divider {
    position: absolute;
    left: 204px;
    top: 28px;
    width: 1px;
    height: 244px;
    background: var(--divider);
  }
  .contact {
    position: absolute;
    left: 222px;
    top: 62px;
    right: 14px;
  }
  .contact-name {
    margin: 0 0 14px;
    font-size: 15px;
    font-weight: 700;
    color: var(--ink-white);
  }
  .contact-list {
    list-style: none;
    margin: 0;
    padding: 0;
  }
  .contact-list li {
    display: flex;
    align-items: center;
    gap: 8px;
    font-size: 11.5px;
    line-height: 18px;
    color: var(--ink-soft);
    white-space: nowrap;
  }
  .contact-list li.social-start {
    margin-top: 14px;
  }
  .icon {
    width: 10px;
    height: 10px;
    flex: none;
    fill: var(--ink-soft);
  }
  .social-mark {
    width: 9px;
    height: 9px;
    flex: none;
    background: var(--ink-soft);
    margin: 0 0.5px;
  }
  /* Front: photo side */
  .card-front {
    left: 630px;
  }
  .front-photo {
    position: absolute;
    inset: 0;
    background:
      radial-gradient(ellipse at 75% 60%, var(--mist-slate) 0%, rgba(76,84,88,0) 55%),
      radial-gradient(ellipse at 30% 15%, var(--mist-teal) 0%, rgba(169,196,196,0) 50%),
      linear-gradient(160deg, var(--mist-light) 0%, #c9d2d4 45%, #7e878b 100%);
  }
  .front-wordmark {
    position: absolute;
    left: 0;
    right: 0;
    top: 130px;
    text-align: center;
    font-size: 30px;
    font-weight: 700;
    letter-spacing: 3px;
    text-transform: uppercase;
    color: var(--logo-dark);
  }
</style>
</head>
<body>
<main class="stage">

  <section class="card card-back" aria-label="Business card back">
    <div class="back-wordmark">Marlow Thread</div>
    <div class="back-divider"></div>
    <div class="contact">
      <h2 class="contact-name">Karen Whitfield</h2>
      <ul class="contact-list">
        <li>
          <svg class="icon" viewBox="0 0 10 10" aria-hidden="true"><path d="M1 3 Q5 0 9 3 L8 4.5 L6.5 4 L6.5 3 Q5 2.5 3.5 3 L3.5 4 L2 4.5 Z M2 5.5 H8 L9 9 H1 Z"/></svg>
          0498716204
        </li>
        <li>
          <svg class="icon" viewBox="0 0 10 10" aria-hidden="true"><path d="M0.5 2 H9.5 V8.5 H0.5 Z" /><path d="M0.8 2.3 L5 5.6 L9.2 2.3" stroke="#0e0e0e" stroke-width="1" fill="none"/></svg>
          info@marlowthread.example.au
        </li>
        <li>
          <svg class="icon" viewBox="0 0 10 10" aria-hidden="true"><g fill="none" stroke="#d8d8d8" stroke-width="1.3" stroke-linecap="round"><path d="M4.2 5.8 L2.6 7.4 A1.3 1.3 0 0 1 1.6 5.4 L3.4 3.6"/><path d="M5.8 4.2 L7.4 2.6 A1.3 1.3 0 0 0 5.4 1.6 L3.6 3.4"/><path d="M6.6 4.6 L8.4 6.4"/></g></svg>
          www.marlowthread.example.au
        </li>
        <li class="social-start">
          <span class="social-mark" aria-hidden="true"></span>
          _marlow_thread_
        </li>
        <li>
          <span class="social-mark" aria-hidden="true"></span>
          www.fakebookexample.com/marlowthreadau/
        </li>
      </ul>
    </div>
  </section>

  <section class="card card-front" aria-label="Business card front">
    <div class="front-photo" role="img" aria-label="Misty photograph in pale grey, soft teal and slate tones"></div>
    <div class="front-wordmark">Marlow Thread</div>
  </section>

</main>
</body>
</html>
```